Brantor Works Business Card

Modern and Professional Business Card for a Med size construction/development company.

See the samples below for the design I like … but I need ideas for incorporating the red company logo while still keeping the clean look of the card samples that are attached.

Logo and tag line on the back … info on the front.

Tagline: Solid Work from the Footing Upward

Target Market(s)

Med-Large General Contractors

Contact Information for Business Card

Brantor Works Limited
42 Fenwick Avenue
Mt. Pearl, NL
A1N 4R9

t: 709-555-0147
f: 709-555-0182
w: www.brantorworks-example.com

Font styles to use
Sans Serif

Colors
fbee3e

Requirements
Must have
• I like the black and yellow designs of the attached samples …. but I'm not sure how to incorporate the red Brantor Works logo into that design??
Nice to have
• Construction safety strips

```html
<!DOCTYPE html>
<html lang="en">
<head>
<meta charset="utf-8">
<title>Brantor Works Business Card</title>
<link rel="stylesheet" href="https://fonts.googleapis.com/css2?family=Lato:wght@400;700&family=Roboto:wght@500;700&display=swap">
<style>
  :root {
    --brand-red: #e41e26;
    --paper: #ffffff;
    --ink: #1f1f1f;
    --backdrop: #d9d9d9;
  }
  * { box-sizing: border-box; margin: 0; padding: 0; }
  html, body { width: 1200px; height: 802px; overflow: hidden; }
  body { background: var(--backdrop); position: relative; font-family: "Lato", sans-serif; }

  .card {
    position: absolute;
    top: 274px;
    width: 441px;
    height: 264px;
    border-radius: 16px;
    overflow: hidden;
    box-shadow: 0 4px 8px rgba(0,0,0,0.35);
  }
  .card--front { left: 136px; background: var(--paper); }
  .card--back { left: 625px; background: var(--brand-red); }

  .front__band {
    position: absolute; left: 382px; top: 0; width: 59px; height: 100%;
    background: var(--brand-red);
  }
  .front__tab {
    position: absolute; left: 330px; top: 72px; width: 94px; height: 105px;
    background: var(--paper); border-radius: 0 8px 8px 0;
  }
  .front__logo {
    position: absolute; left: 243px; top: 85px; width: 170px; height: 80px;
    background: var(--brand-red); border-radius: 8px;
    display: flex; align-items: center; justify-content: center;
  }
  .logo-name {
    font-family: "Lato", sans-serif; font-weight: 700; font-size: 19px;
    color: var(--paper); letter-spacing: 0.5px;
  }
  .logo-name--red { color: var(--brand-red); font-size: 21px; }

  .holder { position: absolute; left: 27px; top: 36px; }
  .holder__name {
    font-family: "Roboto", sans-serif; font-weight: 700; font-size: 16px;
    color: var(--brand-red); line-height: 1;
  }
  .holder__role { font-size: 12.5px; color: var(--ink); line-height: 1.1; }

  .contact { position: absolute; left: 27px; top: 106px; list-style: none; }
  .contact li {
    display: flex; align-items: center; gap: 3px;
    font-size: 12.5px; color: var(--ink); height: 16.5px;
  }
  .contact svg { width: 11px; height: 11px; flex: none; }

  .address { position: absolute; left: 27px; top: 184px; font-size: 12.5px; line-height: 15.5px; color: var(--ink); font-style: normal; }
  .address__company { color: var(--brand-red); }

  .back__logo {
    position: absolute; left: 126px; top: 88px; width: 188px; height: 89px;
    background: var(--paper); border-radius: 9px;
    display: flex; align-items: center; justify-content: center;
  }
  .back__tagline {
    position: absolute; left: 0; right: 0; top: 210px; text-align: center;
    font-family: "Roboto", sans-serif; font-weight: 500; font-size: 11.5px;
    color: var(--paper); text-transform: uppercase; letter-spacing: 0.1px;
  }
</style>
</head>
<body>

<section class="card card--front" aria-label="Card front">
  <div class="front__band"></div>
  <div class="front__tab"></div>
  <div class="front__logo"><span class="logo-name">Brantor Works</span></div>

  <div class="holder">
    <p class="holder__name">MARCUS HALE</p>
    <p class="holder__role">Managing Director</p>
  </div>

  <ul class="contact">
    <li>
      <svg viewBox="0 0 12 12" aria-hidden="true"><path fill="var(--brand-red)" d="M1 4.5C1 2.5 3 1.5 6 1.5s5 1 5 3l-2.2.6-.4-1.4H3.6l-.4 1.4zM2.5 6h7l1 5h-9z"/></svg>
      709-555-0147
    </li>
    <li>
      <svg viewBox="0 0 12 12" aria-hidden="true"><path fill="var(--brand-red)" d="M3 1h6v3H3zM1 5h10v4H9v2H3V9H1zM4 8v2h4V8z"/></svg>
      709-555-0182
    </li>
    <li>
      <svg viewBox="0 0 12 12" aria-hidden="true"><circle cx="6" cy="6" r="5.5" fill="var(--brand-red)"/><path fill="#fff" d="M4 3.5c1 .3 1.6 1 1.3 2-.4.8-1.4.7-1.6 1.6L3 5.5 3.3 4zM7.5 7c.8 0 1.5.5 1.4 1.3L8 9.5 7 8.3z"/></svg>
      www.brantorworks-example.com
    </li>
  </ul>

  <address class="address">
    <span class="address__company">Brantor Works Limited</span><br>
    42 Fenwick Avenue<br>
    Harbour Vale, NL A0B 2K7
  </address>
</section>

<section class="card card--back" aria-label="Card back">
  <div class="back__logo"><span class="logo-name logo-name--red">Brantor Works</span></div>
  <p class="back__tagline">Solid Work from the Footing Upward</p>
</section>

</body>
</html>
```